We need a complete design for our construction company KELTO CONSTRUCTION based in Auckland New Zealand, we need a logo, website, business card, vehicle design etc..
We are a mid to high-end construction company who work mostly on residential projects and some commercial.

What we want to see in the design;
Professional,
Architectural,
Simple,
Alternative,

We want the design to communicate professionalism, high quality wormanship and and quality service.

Target Market(s)

People looking for a quality building/ construction company

Industry/Entity Type

Construction Company

Contact Information for Business Card

KELTO CONSTRUCTION.co.nz
Lino Verasek
lino@keltoconstruction.example.nz
021 5807 462

Logo Text

KELTO CONSTRUCTION

Number of Pages Required

5+ page

Font styles to use
Sans Serif

Colors

Designer to choose colors to be used in the design.

Requirements
Must have
• Must appear high end, professional, quality, be simple, easy to use, give security to potential clients
Nice to have
• high-quality photos of our recent projects
• about us page
• blog page
• contact us page
• high quality content
Should not have
• should not be hard to use and have too much going on.

```html
<!DOCTYPE html>
<html lang="en">
<head>
<meta charset="utf-8">
<title>KELTO CONSTRUCTION</title>
<link href="https://fonts.googleapis.com/css2?family=Lato:wght@400;700;900&display=swap" rel="stylesheet">
<style>
:root{
  --blue:#1b5fd6;
  --blue-dark:#0f3f9e;
  --ink:#222222;
  --text:#6b6b6b;
  --grey:#eeeeee;
  --footer:#111214;
  --white:#ffffff;
}
*{box-sizing:border-box;margin:0;padding:0}
html,body{width:1200px;height:3228px;overflow:hidden}
body{font-family:'Lato',sans-serif;color:var(--text);background:var(--white);position:relative}
.section{position:absolute;left:0;width:1200px}
.btn{display:inline-block;background:var(--blue);color:var(--white);font-size:13px;font-weight:700;letter-spacing:.5px;padding:0 22px;line-height:36px;text-transform:uppercase}
h2.title{font-size:38px;font-weight:700;color:var(--ink);text-align:center}
p{font-size:14.5px;line-height:24px}

/* hero */
.hero{top:0;height:540px}
.hero-photo{position:absolute;inset:0;background:linear-gradient(180deg,#0c1f44 0%,#1e4a9a 35%,#3a78c9 60%,#8fb4dd 80%,#e9c98c 92%,#2b3d5f 100%)}
.hero-shade{position:absolute;inset:0;background:linear-gradient(180deg,rgba(0,0,0,.35),rgba(0,0,0,0) 30%)}
.topbar{position:absolute;top:12px;right:100px;display:flex;gap:40px;font-size:13px;color:var(--white)}
.topbar span{display:flex;align-items:center;gap:8px}
.brand{position:absolute;left:100px;top:44px;font-size:26px;font-weight:900;color:var(--white);letter-spacing:.5px}
.nav{position:absolute;right:100px;top:54px;display:flex;gap:34px;font-size:15px;font-weight:700;color:var(--white)}
.hero-title{position:absolute;top:356px;width:100%;text-align:center;font-size:64px;font-weight:900;color:var(--white);letter-spacing:1px}
.hero .btn{position:absolute;left:524px;top:440px;text-transform:none;font-size:15px;padding:0 28px;line-height:40px}
.arrow{position:absolute;top:246px;width:36px;height:36px;border-radius:50%;background:rgba(255,255,255,.85)}
.arrow.left{left:26px}.arrow.right{right:26px}

/* about */
.about{top:540px;height:388px;text-align:center}
.about h2{margin-top:64px}
.about .copy{width:760px;margin:26px auto 0}
.about .copy p+p{margin-top:12px}
.about .btn{margin-top:32px}

/* why */
.why{top:928px;height:416px;background:var(--grey);overflow:hidden}
.why svg.band{position:absolute;left:0;top:0}
.why-text{position:absolute;left:132px;top:96px;width:390px}
.why-text h2{font-size:38px;color:var(--ink);font-weight:700;margin-bottom:20px}
.why-text p+p{margin-top:12px}
.why-text a{color:var(--blue);font-weight:700}
.why-photo{position:absolute;left:560px;top:120px;width:370px;height:280px;background:linear-gradient(135deg,#8fb0d6,#e8e2d2 45%,#c9b37a 70%,#4d5c6f)}

/* services */
.services{top:1344px;height:836px}
.services h2{margin-top:124px}
.service{position:absolute;width:420px;text-align:center}
.service svg{display:block;margin:0 auto}
.service h3{font-size:19px;font-weight:700;color:var(--ink);margin-top:18px;text-transform:uppercase}
.service p{margin-top:10px;font-size:13.5px;line-height:22px}
.service .btn{margin-top:22px;font-size:12px;line-height:32px;padding:0 18px}

/* projects */
.projects{top:2180px;left:100px;width:1000px;height:480px}
.grid{position:absolute;inset:0;display:grid;grid-template-columns:repeat(4,250px);grid-template-rows:repeat(2,240px)}
.tile{position:relative}
.tile .label{position:absolute;left:0;right:0;top:96px;text-align:center;color:var(--white);font-size:20px;font-weight:700}
.projects-tag{position:absolute;left:0;top:12px;height:60px;width:360px}
.projects-tag span{position:absolute;left:28px;top:13px;font-size:28px;font-weight:700;color:var(--white)}

/* footer */
.footer{top:2740px;height:488px;background:var(--footer);color:#cfcfcf}
.footer-photo{position:absolute;left:0;top:0;width:600px;height:440px;background:linear-gradient(90deg,#1f2a38 0%,#34465c 40%,rgba(17,18,20,1) 100%)}
.footer h4{font-size:18px;font-weight:700;color:var(--white);text-transform:uppercase;letter-spacing:.5px}
.contact{position:absolute;left:632px;top:72px;width:300px}
.contact ul{list-style:none;margin-top:18px}
.contact li{display:flex;gap:12px;font-size:13px;line-height:20px;margin-bottom:14px}
.contact svg{flex:none;margin-top:2px}
.links{position:absolute;left:972px;top:72px}
.links ul{list-style:none;margin-top:18px}
.links li{font-size:13px;line-height:26px;display:flex;align-items:center;gap:10px}
.links li::before{content:"";width:5px;height:5px;border-radius:50%;background:var(--white)}
.newsletter{position:absolute;left:632px;top:300px}
.subscribe{display:flex;margin-top:16px}
.subscribe .field{width:280px;height:34px;background:var(--white);color:#999;font-size:12px;line-height:34px;padding-left:12px}
.subscribe .send{height:34px;background:var(--blue);color:var(--white);font-size:11px;font-weight:700;line-height:34px;padding:0 14px}
.bottombar{position:absolute;left:0;bottom:0;width:1200px;height:48px;background:#0a0a0b;font-size:12px;color:#9a9a9a}
.bottombar .copy{position:absolute;left:100px;top:16px}
.social{position:absolute;right:100px;top:14px;display:flex;gap:8px}
.social i{display:block;width:20px;height:20px;background:var(--blue)}
.social i:nth-child(3){background:#c0392b}
</style>
</head>
<body>

<section class="section hero">
  <div class="hero-photo" role="img" aria-label="Upward view of modern glass office towers against a blue sky with sunlight"></div>
  <div class="hero-shade"></div>
  <div class="topbar">
    <span><svg width="12" height="12" viewBox="0 0 24 24"><path fill="#fff" d="M6.6 10.8a15 15 0 0 0 6.6 6.6l2.2-2.2a1 1 0 0 1 1-.25 11 11 0 0 0 3.6.6 1 1 0 0 1 1 1V20a1 1 0 0 1-1 1A17 17 0 0 1 3 4a1 1 0 0 1 1-1h3.5a1 1 0 0 1 1 1 11 11 0 0 0 .6 3.6 1 1 0 0 1-.25 1z"/></svg>+1 963 555 0148</span>
    <span><svg width="13" height="10" viewBox="0 0 26 20"><rect x="1" y="1" width="24" height="18" fill="none" stroke="#fff" stroke-width="2"/><path d="M1 1l12 10 12-10" fill="none" stroke="#fff" stroke-width="2"/></svg>info@keltoconstruction.example.nz</span>
  </div>
  <div class="brand">KELTO CONSTRUCTION</div>
  <nav class="nav"><span>Home</span><span>About us</span><span>Projects</span><span>Blog</span><span>Contact us</span>
    <svg width="16" height="16" viewBox="0 0 24 24"><circle cx="10" cy="10" r="7" fill="none" stroke="#fff" stroke-width="3"/><path d="M15 15l7 7" stroke="#fff" stroke-width="3"/></svg></nav>
  <div class="arrow left"><svg width="36" height="36"><path d="M21 11l-7 7 7 7" fill="none" stroke="#333" stroke-width="3"/></svg></div>
  <div class="arrow right"><svg width="36" height="36"><path d="M15 11l7 7-7 7" fill="none" stroke="#333" stroke-width="3"/></svg></div>
  <h1 class="hero-title">KELTO CONSTRUCTION</h1>
  <span class="btn">Request Quote</span>
</section>

<section class="section about">
  <h2 class="title">About Us</h2>
  <div class="copy">
    <p>We are a mid to high-end building company based in Auckland, crafting homes and commercial spaces with care. Every project is led by a small team of skilled builders who value clear planning, honest pricing and precise workmanship from the first site visit to the final handover.</p>
    <p>Our clients trust us because we listen, communicate openly and deliver on time. We work closely with architects and engineers to turn considered designs into lasting buildings that feel solid, calm and beautifully finished.</p>
  </div>
  <span class="btn">Read More</span>
</section>

<section class="section why">
  <svg class="band" width="1200" height="416"><polygon points="820,0 1200,0 1200,416 650,416 560,330 560,100" fill="var(--blue)"/><polygon points="1000,0 1200,0 1200,200" fill="var(--blue-dark)"/></svg>
  <div class="why-text">
    <h2>Why Choose Us</h2>
    <p>We bring years of residential experience and a steady focus on quality.</p>
    <p>From concept to completion we manage every detail, keep sites tidy and safe, and stay in touch through each stage so you always know where your build stands. Our standards are high because your home deserves nothing less. <a>Read More</a></p>
  </div>
  <div class="why-photo" role="img" aria-label="Builders in hard hats and safety vests reviewing plans on site"></div>
</section>

<section class="section services">
  <h2 class="title">Our Services</h2>
  <div class="service" style="left:118px;top:222px">
    <svg width="36" height="44" viewBox="0 0 36 44"><rect x="4" y="6" width="28" height="36" fill="none" stroke="var(--blue)" stroke-width="3"/><path d="M12 6V2h12v4M12 14v24M18 14v24M24 14v24" stroke="var(--blue)" stroke-width="3"/></svg>
    <h3>Construction Management</h3>
    <p>Clear programmes, careful budgets and one point of contact keep your project moving smoothly from start to finish.</p>
    <span class="btn">Read More</span>
  </div>
  <div class="service" style="left:662px;top:222px">
    <svg width="40" height="44" viewBox="0 0 40 44"><path d="M20 2L2 18h6v24h24V18h6z" fill="var(--blue)"/><rect x="16" y="26" width="8" height="16" fill="#fff"/></svg>
    <h3>Building Information Modeling</h3>
    <p>Detailed digital models help us coordinate trades early, avoid surprises on site and deliver accurate results.</p>
    <span class="btn">Read More</span>
  </div>
  <div class="service" style="left:118px;top:542px">
    <svg width="40" height="40" viewBox="0 0 40 40"><rect x="2" y="6" width="30" height="32" fill="none" stroke="var(--blue)" stroke-width="3"/><path d="M14 26l22-22 3 3-22 22-5 2z" fill="var(--blue)"/></svg>
    <h3>Design Build</h3>
    <p>Design and construction under one roof means fewer handovers, faster decisions and a home built as planned.</p>
    <span class="btn">Read More</span>
  </div>
  <div class="service" style="left:662px;top:542px">
    <svg width="40" height="40" viewBox="0 0 40 40"><path d="M6 34L26 14" stroke="var(--blue)" stroke-width="6"/><path d="M22 4a8 8 0 0 0 10 10l4-4" fill="none" stroke="var(--blue)" stroke-width="4"/><path d="M8 6l26 28" stroke="var(--blue)" stroke-width="5"/></svg>
    <h3>General Contracting</h3>
    <p>We manage subcontractors, materials and inspections so every stage meets code and our own higher standard.</p>
    <span class="btn">Read More</span>
  </div>
</section>

<section class="section projects">
  <div class="grid">
    <div class="tile" role="img" aria-label="Modern apartment building exterior" style="background:linear-gradient(160deg,#cfd8e2,#8c9aab)"></div>
    <div class="tile" role="img" aria-label="Residential building at dusk" style="background:linear-gradient(160deg,#2b3340,#4c5868)"><div class="label">Residential Buildings</div></div>
    <div class="tile" role="img" aria-label="Bright open-plan interior" style="background:linear-gradient(160deg,#e8e4dc,#b8ad9c)"></div>
    <div class="tile" role="img" aria-label="Contemporary house with garden" style="background:linear-gradient(160deg,#9cc0e0,#dfe5e8 55%,#7f9c5a)"></div>
    <div class="tile" role="img" aria-label="Glass facade of office block" style="background:linear-gradient(160deg,#a9c4de,#5d7a99)"></div>
    <div class="tile" role="img" aria-label="White residential apartments" style="background:linear-gradient(160deg,#e6ebef,#a7b3bd)"></div>
    <div class="tile" role="img" aria-label="Modern home exterior with paving" style="background:linear-gradient(160deg,#8fa8be,#d8d2c6 60%,#6c6a62)"></div>
    <div class="tile" role="img" aria-label="Family house with lawn" style="background:linear-gradient(160deg,#a9c9e6,#ece8de 55%,#6f9448)"></div>
  </div>
  <svg class="projects-tag" width="360" height="60"><polygon points="0,0 360,0 310,60 0,60" fill="var(--blue)"/></svg>
  <div class="projects-tag" style="background:none"><span>Our Projects</span></div>
</section>

<footer class="section footer">
  <div class="footer-photo" role="img" aria-label="Faded view of a glass building facade"></div>
  <div class="contact">
    <h4>Contact Now</h4>
    <ul>
      <li><svg width="12" height="16" viewBox="0 0 12 16"><path d="M6 0a6 6 0 0 0-6 6c0 4.5 6 10 6 10s6-5.5 6-10a6 6 0 0 0-6-6z" fill="#fff"/><circle cx="6" cy="6" r="2" fill="#111"/></svg>1st floor, Kelto Construction,<br>Auckland, New Zealand</li>
      <li><svg width="14" height="11" viewBox="0 0 26 20"><rect x="1" y="1" width="24" height="18" fill="none" stroke="#fff" stroke-width="2"/><path d="M1 1l12 10 12-10" fill="none" stroke="#fff" stroke-width="2"/></svg>info@keltoconstruction.example.nz</li>
      <li><svg width="13" height="13" viewBox="0 0 24 24"><path fill="#fff" d="M6.6 10.8a15 15 0 0 0 6.6 6.6l2.2-2.2a1 1 0 0 1 1-.25 11 11 0 0 0 3.6.6 1 1 0 0 1 1 1V20a1 1 0 0 1-1 1A17 17 0 0 1 3 4a1 1 0 0 1 1-1h3.5a1 1 0 0 1 1 1 11 11 0 0 0 .6 3.6 1 1 0 0 1-.25 1z"/></svg>+1 963 555 0148</li>
    </ul>
  </div>
  <div class="links">
    <h4>Quick Links</h4>
    <ul><li>Home</li><li>About Us</li><li>Projects</li><li>Blog</li><li>Contact Us</li></ul>
  </div>
  <div class="newsletter">
    <h4>Newsletter</h4>
    <div class="subscribe"><span class="field">Email Address</span><span class="send">SEND</span></div>
  </div>
  <div class="bottombar">
    <span class="copy">© 2018 Copyrights. KELTO CONSTRUCTION. All rights reserved.</span>
    <div class="social"><i></i><i></i><i></i><i></i></div>
  </div>
</footer>

</body>
</html>
```